i NEED A MY CURRENT LOGO UPDATED TO MAKE IT LOOK MORE MODERN. I WANT TO KEEP MY CURRENT COLOURS FOR THE LOGO WHICH ARE GREEN, BLACK, WHITE AND SILVER/METALIC COLOURS.

I RUN A BUSINESS WHICH IS CALLED "CONVEYANCING" IN AUSTRALIA. THIS BUSINESS PROVIDES A SERVICES FOR PEOPLE WHO ARE BUYING OR SELLING OR TRANSFER THEIR PROPERTY. WE ARE NOT A REAL ESTATE AGENT. WE PREPARE AND DO ALL WORK NECESSARY TO COMPLETE A LEGAL TRANSFER OF PROPERTY FOR CUSTOMERS. THE REASON i CHOSE THE NAME "BRELMOR CONVEYANCING" IS BECAUSE WE CAN ONLY DO VICTORIAN PROPERTY TRANSFERS AND IN AUSTRALIA THE LAND IS TRANSFERED TO AN OWNER AND WHATEVER IS ON THE LAND BECOMES THE OWNERS.

MY LOGO MUST HAVE THE VICTORIAN STATE AS A SYMBOL (VICTORIA IS ONE OF THE STATES IN AUSTRALIA AND IT'S KNOWN AS A GREEN STATE). I CAN EMAIL YOU THE CURRENT LOGO TO GIVE YOU AN IDEA.

I'M HAPPY WITH THE CURRENT COLOURS BUT NOT THE LAYOUT OR DESIGN. AT THE MOMENT IT'S PRETTY PLAIN AND BORING.

Example - This is a creative design I copied from the net.

Hi All, I've posted a design in which I would like you to consider being creative with the victorian logo as they have done with the swan here.  Just an idea.

Hi All, I just wanted to let you know that other than the colours I requested I want you all to come up with your own idea of the logo.  So far this is the only create design I've seen. 

Target Market(s)

People that are in the market to buy or selling property/real estate.

Industry/Entity Type

Business

Requirements
Must have
• THE COLOURS MUST REMAIN THE SAME AND MUST BE PROFESSIONAL AS WE ARE A PART OF THE LEGAL (PROFESSIONAL)INDUSTRY IN AUSTRALIA
Nice to have
• MUST HAVE THE VICTORIAN LOGO/SYMBOL
Should not have
• SHOULD NOT BE BORING. THE DETAILS OF OUR ADDRESS ON THE ATTACHED IS OLD DETAILS NOT OUR CURRENT DETAILS. IT'S ATTACHED TO SHOW YOU AN EXAMPLE OF THE CURRENT LOGO.

```html
<!DOCTYPE html>
<html lang="en">
<head>
<meta charset="utf-8">
<title>Brelmor Conveyancing – Business Cards</title>
<link rel="stylesheet" href="https://fonts.googleapis.com/css2?family=Alegreya:wght@400&family=Source+Sans+3:wght@400&display=swap">
<style>
  :root {
    --backdrop: #f1e8df;
    --card: #ffffff;
    --ink: #2b2b2b;
    --silver: #9a9a9a;
    --rule: #b8b8b8;
    --green: #2f8a45;
    --shadow: rgba(90, 70, 50, 0.18);
  }
  * { margin: 0; padding: 0; box-sizing: border-box; }
  html, body {
    width: 1200px;
    height: 704px;
    overflow: hidden;
    background: var(--backdrop);
  }
  .stage {
    position: relative;
    width: 1200px;
    height: 704px;
  }
  .card {
    position: absolute;
    width: 515px;
    height: 285px;
    background: var(--card);
    box-shadow: 0 3px 10px var(--shadow);
  }
  .card--front { left: 90px; top: 300px; }
  .card--back  { left: 595px; top: 125px; }

  .brand {
    position: absolute;
    display: flex;
    align-items: center;
    gap: 9px;
    font-family: "Source Sans 3", sans-serif;
    font-weight: 400;
    color: var(--ink);
    white-space: nowrap;
  }
  .brand__mark {
    width: 14px;
    height: 14px;
    background: var(--green);
  }
  .card--front .brand { left: 196px; top: 100px; font-size: 23px; }
  .card--back .brand  { left: 0; right: 0; justify-content: center; top: 140px; font-size: 23px; }

  .holder {
    position: absolute;
    right: 332px;
    top: 140px;
    text-align: right;
    font-family: "Alegreya", serif;
    font-size: 21px;
    line-height: 23px;
    color: var(--silver);
  }
  .divider {
    position: absolute;
    left: 197px;
    top: 145px;
    width: 1px;
    height: 105px;
    background: var(--rule);
  }
  .contact {
    position: absolute;
    left: 212px;
    top: 146px;
    font-family: "Alegreya", serif;
    font-size: 14px;
    line-height: 18px;
    color: var(--ink);
  }
  .contact__lines + .contact__lines { margin-top: 16px; }

  .notice {
    position: absolute;
    left: 0;
    right: 0;
    top: 196px;
    text-align: center;
    font-family: "Source Sans 3", sans-serif;
    font-size: 11.5px;
    line-height: 17px;
    color: var(--ink);
  }
</style>
</head>
<body>
<main class="stage">
  <section class="card card--front" aria-label="Business card front">
    <div class="brand"><span class="brand__mark"></span><span>Brelmor Conveyancing</span></div>
    <p class="holder">Lena<br>Haddad</p>
    <span class="divider"></span>
    <div class="contact">
      <p class="contact__lines">14 Carrow Street<br>Kelbrook Park Victoria 3099</p>
      <p class="contact__lines">Tel: (03)9412 5530<br>Fax: (03) 0000 000<br>email: brelmorconveyancing@mailbox.com</p>
    </div>
  </section>

  <section class="card card--back" aria-label="Business card back">
    <div class="brand"><span class="brand__mark"></span><span>Brelmor Conveyancing</span></div>
    <p class="notice">
      This firm holds profesional indemnity insurance against civil liability.<br>
      A solicitor is employed by this film for all legal work.<br>
      Professional Indemnity.
    </p>
  </section>
</main>
</body>
</html>
```